Business Card for beauty technology startup

Design Glimora Business Card for a Beauty, based on the website identity and colors (https://www.glimora-example.com).
Glimora is a beauty tech startup that gathers helpful product info for beauty lovers and consumers (such as availability on stores, price range and product reviews) for makeup products. The card design must be young, colorful but clean, and very modern.

Target Market(s)

woman, 15-35

Industry/Entity Type

Cosmetics

Contact Information for Business Card

Full Name, address, phone

Font styles to use
Other font styles liked:
• Advent Pro

Colors
e34297
86cfc6
ffffff
5c5c5c
e8e8e8
e667a6
b2b2b2

Requirements
Must have
• One full colored side with a creative design and another with card info
• Use Color palette: #95C5C5 and/or #D38AA5
• Use fonts: Advent Pro
• Use website identity: https://www.glimora-example.com
Nice to have
• If needed extra font: Roboto

```html
<!DOCTYPE html>
<html lang="en">
<head>
<meta charset="utf-8">
<title>Glimora Business Card</title>
<link rel="stylesheet" href="https://fonts.googleapis.com/css2?family=Advent+Pro:wght@300;400&family=Roboto:wght@400;500&family=Roboto+Condensed:wght@500&display=swap">
<style>
  :root {
    --page-bg: #e8e8e8;
    --card-dark: #18191b;
    --card-pink: #c4829a;
    --accent-pink: #c98aa5;
    --accent-pink-light: #e6a9bf;
    --back-text: #f3bfd2;
    --white: #ffffff;
  }
  * { margin: 0; padding: 0; box-sizing: border-box; }
  html, body { width: 1200px; height: 960px; overflow: hidden; }
  body {
    position: relative;
    background: var(--page-bg);
    font-family: "Roboto", Arial, sans-serif;
  }
  .card {
    position: absolute;
    width: 598px;
    height: 342px;
    border-radius: 18px;
  }
  .card-front { left: 315px; top: 113px; background: var(--card-dark); }
  .card-back { left: 312px; top: 472px; background: var(--card-pink); }

  .brand-mark {
    position: absolute;
    border-radius: 50%;
    border: 2px solid var(--accent-pink);
  }
  .card-front .brand-mark { left: 28px; top: 42px; width: 54px; height: 54px; }
  .brand-name {
    position: absolute;
    font-family: "Advent Pro", sans-serif;
    font-weight: 300;
    color: var(--accent-pink);
    letter-spacing: 5px;
    line-height: 1;
  }
  .card-front .brand-name { left: 127px; top: 52px; font-size: 50px; }

  .holder { position: absolute; right: 28px; top: 72px; text-align: right; }
  .holder-name {
    font-family: "Roboto Condensed", sans-serif;
    font-weight: 500;
    font-size: 22px;
    color: var(--accent-pink);
    line-height: 1;
  }
  .holder-title { margin-top: 6px; font-size: 14px; color: var(--white); letter-spacing: .3px; }

  .divider {
    position: absolute;
    left: 30px; right: 28px; top: 129px;
    height: 3px;
    background: linear-gradient(90deg, #b9788f, #e6a9bf 50%, #b9788f);
  }

  .contact-list {
    position: absolute; left: 30px; top: 221px;
    list-style: none;
    font-size: 14px; color: var(--white);
  }
  .contact-list li { display: flex; align-items: center; height: 19px; }
  .contact-list svg { width: 13px; height: 13px; margin-right: 8px; fill: var(--accent-pink); }

  .address {
    position: absolute; right: 28px; top: 243px;
    text-align: right; font-size: 14px; color: var(--white); line-height: 18.5px;
  }
  .address .web { letter-spacing: 1px; }

  .card-back .brand-mark {
    left: 247px; top: 79px; width: 106px; height: 106px;
    border-color: var(--back-text);
  }
  .card-back .brand-name {
    left: 0; right: 0; top: 213px; text-align: center;
    font-size: 48px; color: var(--back-text); letter-spacing: 6px;
  }
  .back-web {
    position: absolute; left: 0; right: 0; top: 294px;
    text-align: center; font-size: 14px; letter-spacing: 4px; color: var(--back-text);
  }
</style>
</head>
<body>
  <section class="card card-front">
    <span class="brand-mark"></span>
    <div class="brand-name">GLIMORA</div>
    <div class="holder">
      <div class="holder-name">CLARA HENSLEY</div>
      <div class="holder-title">CEO/FOUNDER</div>
    </div>
    <div class="divider"></div>
    <ul class="contact-list">
      <li><svg viewBox="0 0 16 16"><path d="M3 1l3 3-1.5 2c1 2 3 4 5.5 5.5L12 10l3 3-2 2C7 15 1 9 1 3z"/></svg>555 210 4817</li>
      <li><svg viewBox="0 0 16 16"><path d="M4 0h8v16H4zM5.5 2v10h5V2zM7 13.5h2v1H7z" fill-rule="evenodd"/></svg>555 372 6093</li>
      <li><svg viewBox="0 0 16 16"><path d="M4 1h8v4H4zM1 6h14v6h-2v3H3v-3H1zM4.5 10v3.5h7V10z" fill-rule="evenodd"/></svg>555 648 2251</li>
      <li><svg viewBox="0 0 16 16"><path d="M1 3h14v10H1zM2 4.5v.5l6 4 6-4v-.5z" fill-rule="evenodd"/></svg>info@glimora-example.com</li>
    </ul>
    <div class="address">
      214 Linden Court<br>
      Fairbanks, Alaska 99701<br>
      <span class="web">www.glimora-example.com</span>
    </div>
  </section>

  <section class="card card-back">
    <span class="brand-mark"></span>
    <div class="brand-name">GLIMORA</div>
    <div class="back-web">www.glimora-example.com</div>
  </section>
</body>
</html>
```